Harbor Loom Floors Letterhead

Letterhead used for business reasons. It must be editable and easy to use.

Address is 2715 W. Pelican Lane Marlow Bay GA 34187 - 586.382.6519

```html
<!DOCTYPE html>
<html lang="en">
<head>
<meta charset="utf-8">
<title>Harbor Loom Floors Letterhead</title>
<link rel="stylesheet" href="https://fonts.googleapis.com/css2?family=Open+Sans:wght@300;400&family=Pinyon+Script&display=swap">
<style>
  :root {
    --brand-orange: #d4811e;
    --ink: #333333;
    --ink-muted: #666666;
    --paper: #f3f3f3;
    --backdrop: #e2e2e2;
  }
  * { box-sizing: border-box; margin: 0; padding: 0; }
  html, body {
    width: 1200px;
    height: 1200px;
    overflow: hidden;
    background: var(--backdrop);
    font-family: "Open Sans", Arial, sans-serif;
  }
  .letterhead {
    position: absolute;
    left: 210px;
    top: 48px;
    width: 780px;
    height: 1103px;
    background: var(--paper);
    box-shadow: 0 2px 8px rgba(0,0,0,0.12);
  }
  .brand-name {
    position: absolute;
    top: 36px;
    left: 0;
    width: 100%;
    text-align: center;
    font-weight: 400;
    font-size: 32px;
    letter-spacing: 0.5px;
    color: var(--brand-orange);
  }
  .letter-body {
    position: absolute;
    left: 105px;
    top: 256px;
    width: 570px;
    font-weight: 300;
    font-size: 13.2px;
    line-height: 18.3px;
    color: var(--ink);
  }
  .salutation { margin-bottom: 18px; }
  .letter-body p.paragraph {
    text-align: justify;
    margin-bottom: 18px;
  }
  .closing {
    position: absolute;
    left: 105px;
    top: 753px;
    font-weight: 300;
    font-size: 13.2px;
    color: var(--ink);
  }
  .signature {
    position: absolute;
    left: 110px;
    top: 776px;
    font-family: "Pinyon Script", cursive;
    font-size: 27px;
    color: #222;
  }
  .contact {
    position: absolute;
    left: 68px;
    top: 1007px;
    font-size: 13px;
    line-height: 16px;
    font-style: normal;
    color: var(--ink-muted);
  }
  .contact .phone { display: flex; align-items: center; gap: 6px; }
  .contact .phone svg { width: 11px; height: 11px; }
  .website {
    position: absolute;
    right: 68px;
    top: 1040px;
    font-size: 13px;
    color: var(--ink-muted);
  }
  .website .domain { color: var(--brand-orange); }
  .footer-band {
    position: absolute;
    left: 0;
    bottom: 0;
    width: 100%;
    height: 15px;
    background: var(--brand-orange);
  }
</style>
</head>
<body>
  <main class="letterhead">
    <header class="brand-name">Harbor Loom Floors</header>

    <section class="letter-body">
      <p class="salutation">Dear Daniel Whitcombe,</p>
      <p class="paragraph">Lorem ipsum dolor sit amet, consectetuer adipiscing elit, sed diam nonummy nibh euismod tincidunt ut laoreet dolore magna aliquam erat volutpat. Ut wisi enim ad minim veniam, quis nostrud exerci tation ullamcorper suscipit lobortis nisl ut aliquip ex ea commodo consequat. Duis dolore te feugait nulla facilisi. Nam liber tempor cum soluta nobis eleifend option congue nihil imperdiet doming id quod mazim placerat facer possim assum. Lorem ipsum dolor sit amet, consectetuer adipiscing elit, sed diam nonummy nibh euismod tincidunt ut laoreet dolore magna aliquam erat volutpat. Ut wisi enim ad minim veniam, quis nostrud exerci tation ullamcorper suscipit lobortis nisl ut aliquip ex ea commodo consequat.</p>
      <p class="paragraph">Consectetuer adipiscing elit, sed diam nonummy nibh euismod tincidunt ut laoreet dolore magna aliquam erat volutpat. Ut wisi enim ad minim veniam, quis nostrud exerci tation ullamcorper suscipit lobortis nisl ut aliquip ex ea commodo consequat. Consectetuer adipiscing elit, sed diam nonummy nibh euismod tincidunt ut laoreet dolore magna aliquam erat volutpat. Ut wisi enim ad minim veniam, quis nostrud exerci tation ullamcorper suscipit lobortis nisl ut aliquip ex ea commodo consequat.</p>
      <p class="paragraph">Consectetuer adipiscing elit, sed diam nonummy nibh euismod tincidunt ut laoreet dolore magna aliquam erat volutpat. Ut wisi enim ad minim veniam, quis nostrud exerci tation ullamcorper suscipit lobortis nisl ut aliquip ex ea commodo consequat. Consectetuer adipiscing elit, sed diam nonummy nibh euismod tincidunt ut laoreet dolore magna aliquam erat volutpat. Ut wisi enim ad minim veniam, quis nostrud exerci tation ullamcorper suscipit lobortis nisl ut aliquip ex ea commodo consequat.</p>
    </section>

    <p class="closing">Sincerely Yours</p>
    <p class="signature">Marcus Ellery</p>

    <address class="contact">
      <span class="phone">
        <svg viewBox="0 0 24 24" aria-hidden="true"><path fill="#d4811e" d="M6.6 10.8a15.1 15.1 0 0 0 6.6 6.6l2.2-2.2a1 1 0 0 1 1-.25 11.4 11.4 0 0 0 3.6.57 1 1 0 0 1 1 1V20a1 1 0 0 1-1 1A17 17 0 0 1 3 4a1 1 0 0 1 1-1h3.5a1 1 0 0 1 1 1c0 1.25.2 2.45.57 3.57a1 1 0 0 1-.25 1z"/></svg>
        586.382.6519
      </span>
      <span>2715 W. Pelican Lane</span><br>
      <span>Marlow Bay GA 34187</span>
    </address>

    <p class="website">www.<span class="domain">harborloomfloors</span>.com</p>

    <div class="footer-band"></div>
  </main>
</body>
</html>
```